Business Card For Halvenmoor Financial Consulting

Hi, I would like a business card designed. Bold, modern.
Please use the same design as the logo. I have also attached the website design to see the overall theme.
Wordmark Font
Color: Hex: #01AEF7

```html
<!DOCTYPE html>
<html lang="en">
<head>
<meta charset="utf-8">
<title>Halvenmoor Financial Consulting – Business Card</title>
<link rel="stylesheet" href="https://fonts.googleapis.com/css2?family=Montserrat:wght@700&family=Open+Sans:wght@400;700&display=swap">
<style>
  :root {
    --stage: #1b1c1e;
    --card-navy: #064370;
    --card-deep: #053d66;
    --accent: #3ba9e0;
    --white: #ffffff;
  }
  * { box-sizing: border-box; margin: 0; padding: 0; }
  html, body {
    width: 1200px;
    height: 801px;
    overflow: hidden;
    background: var(--stage);
  }
  .stage {
    width: 1200px;
    height: 801px;
    display: flex;
    align-items: center;
    justify-content: center;
    gap: 50px;
  }
  .card {
    width: 530px;
    height: 305px;
    background: var(--card-navy);
    border-bottom: 3px solid var(--accent);
    position: relative;
    overflow: hidden;
    flex: none;
  }
  /* Front: contact side */
  .card--front { display: flex; }
  .front-info {
    width: 56%;
    padding: 30px 0 0 30px;
    color: var(--white);
    font-family: "Open Sans", sans-serif;
  }
  .wordmark {
    display: flex;
    align-items: center;
    gap: 10px;
    font-family: "Montserrat", sans-serif;
    font-weight: 700;
    color: var(--white);
    text-transform: uppercase;
    line-height: 1.1;
  }
  .wordmark__square {
    width: 16px;
    height: 16px;
    background: var(--accent);
    flex: none;
  }
  .wordmark--small { font-size: 15px; letter-spacing: 0.6px; }
  .person { margin-top: 22px; }
  .person__name {
    font-weight: 700;
    font-size: 19px;
    letter-spacing: 0.6px;
    text-transform: uppercase;
    line-height: 1.2;
  }
  .person__role { font-size: 14px; }
  .address { margin-top: 12px; font-size: 14px; line-height: 1.35; }
  .contacts { margin-top: 12px; list-style: none; font-size: 14px; line-height: 1.5; }
  .contacts li { display: flex; align-items: center; gap: 8px; }
  .contacts svg { width: 12px; height: 12px; flex: none; }
  .front-panel {
    width: 44%;
    display: flex;
    align-items: center;
    justify-content: center;
  }
  .front-panel__square {
    width: 190px;
    height: 190px;
    background: var(--accent);
  }
  /* Back: brand side */
  .card--back {
    display: flex;
    align-items: center;
    justify-content: center;
  }
  .wordmark--large { font-size: 33px; letter-spacing: 1px; gap: 16px; }
  .wordmark--large .wordmark__square { width: 30px; height: 30px; }
</style>
</head>
<body>
<main class="stage">
  <section class="card card--front" aria-label="Business card front">
    <div class="front-info">
      <div class="wordmark wordmark--small">
        <span class="wordmark__square"></span>
        <span>Halvenmoor Financial<br>Consulting</span>
      </div>
      <div class="person">
        <p class="person__name">Nadia Kerr</p>
        <p class="person__role">Managing Director</p>
      </div>
      <p class="address">Your address, City<br>State, Zip 1234</p>
      <ul class="contacts">
        <li>
          <svg viewBox="0 0 12 12" aria-hidden="true"><path fill="#3ba9e0" d="M2.5 1l2 2.2-1 1.3a7 7 0 0 0 4 4l1.3-1 2.2 2-1.4 1.5C5.4 10.8 1.2 6.6 1 2.4z"/></svg>
          123 456 789
        </li>
        <li>
          <svg viewBox="0 0 12 12" aria-hidden="true"><rect x="1" y="2.5" width="10" height="7" fill="#3ba9e0"/><path d="M1 2.5l5 4 5-4" stroke="#064370" fill="none"/></svg>
          info@yourgmail.com
        </li>
        <li>
          <svg viewBox="0 0 12 12" aria-hidden="true"><circle cx="6" cy="6" r="5" fill="none" stroke="#3ba9e0" stroke-width="1.4"/><path d="M1 6h10M6 1c-2.5 3-2.5 7 0 10M6 1c2.5 3 2.5 7 0 10" stroke="#3ba9e0" fill="none" stroke-width="0.9"/></svg>
          www.yourwebsite.com
        </li>
      </ul>
    </div>
    <div class="front-panel">
      <span class="front-panel__square"></span>
    </div>
  </section>

  <section class="card card--back" aria-label="Business card back">
    <div class="wordmark wordmark--large">
      <span class="wordmark__square"></span>
      <span>Halvenmoor<br>Financial Consulting</span>
    </div>
  </section>
</main>
</body>
</html>
```